FinTech company looking to revamp and expand client-facing interface for our financial models

Pellworth Engines currently has a very simple website that allows clients to interact with our financial models. We are looking to completely redesign the current site and add several extra pages to provide extra functionality. We want the design to have a modern, slick feel, that will work on both a desktop or a tablet. It should be straightforward for clients to move between different pages at any time, and clear from the layout how to interact with the more advanced features. We have included screenshots of existing pages in the attached design brief, as well as sketches of the functionality required by the new pages, but can't provide a direct link to the current site.
Target Market(s)
Professional investors that will be paying to access the interface
Industry/Entity Type
Finance
Number of Pages Required
4 page
Colors
Designer to choose colors to be used in the design.
Look and feel
Each slider illustrates characteristics of the customer's brand and the style your logo design should communicate.

```html
<!DOCTYPE html>
<html lang="en">
<head>
<meta charset="utf-8">
<title>Pellworth Engines – Backtest</title>
<link rel="stylesheet" href="https://fonts.googleapis.com/css2?family=Open+Sans:wght@400;600;700&family=Montserrat:wght@500;600&family=Roboto+Condensed:wght@400&display=swap">
<style>
:root{
  --frame:#ffffff;
  --page:#ebebeb;
  --navy:#0b3566;
  --ink:#111111;
  --black:#1a1a1a;
  --tab:#ffffff;
  --row-alt:#f0f0f0;
  --grid:#e6e6e6;
  --axis:#8a8a8a;
  --blue:#3a6fb0;
  --olive:#b7b53b;
  --green:#4a9a2e;
  --dark-tab:#2f2f2f;
}
*{box-sizing:border-box;margin:0;padding:0}
html,body{width:1200px;height:1122px;overflow:hidden;background:var(--frame)}
body{position:relative;font-family:"Open Sans",sans-serif;color:var(--ink)}
.page{position:absolute;left:14px;top:14px;width:1172px;height:1094px;background:var(--page)}
.topnav{position:absolute;left:14px;top:14px;width:1172px;height:56px;background:#fff;display:flex;border-bottom:1px solid #e2e2e2}
.topnav .item{height:56px;display:flex;align-items:center;justify-content:center;gap:8px;font-size:13px;font-weight:700;border-right:1px solid #ececec}
.topnav .brand{width:166px;font-size:16px;letter-spacing:.3px}
.topnav .term{width:83px}
.topnav .spacer{width:125px}
.topnav .models{width:129px;border-left:1px solid #ececec}
.topnav .sens{width:164px}
.topnav .port{width:147px}
.topnav .backtest{width:140px;background:var(--navy);color:#fff;border-right:none}
.topnav svg{display:block}
.chart-card{position:absolute;left:97px;top:106px;width:1071px;height:393px;background:#fff;box-shadow:0 2px 8px rgba(0,0,0,.12);overflow:hidden}
.chart-card .tabbar{position:absolute;left:0;top:0;width:100%;height:79px;background:#efefef;box-shadow:0 4px 8px rgba(0,0,0,.06)}
.tab{position:absolute;top:46px;height:33px;display:flex;align-items:center;justify-content:center;font-size:12px;font-weight:600;background:var(--tab);color:#555}
.tab.chart{left:51px;width:143px;background:var(--navy);color:#fff}
.tab.t1{left:199px;width:82px}
.tab.t2{left:286px;width:83px}
.tab.t3{left:374px;width:82px;top:41px;height:38px}
.tab.t4{left:461px;width:83px;top:37px;height:42px;background:var(--black);color:#fff;border-radius:3px 3px 0 0;align-items:flex-start;padding-top:13px}
.plot{position:absolute;left:0;top:0}
.options{position:absolute;left:14px;top:376px;width:46px;height:230px;background:var(--dark-tab);border-radius:0 4px 4px 0}
.options span{position:absolute;left:23px;top:115px;transform:translate(-50%,-50%) rotate(-90deg);color:#fff;font-size:16px;letter-spacing:1px;white-space:nowrap}
.options .toggle{position:absolute;left:33px;top:104px}
.export{position:absolute;top:546px;display:flex;align-items:center;gap:7px;color:var(--navy);font-family:"Montserrat",sans-serif;font-weight:600;font-size:16px}
.export.left{left:382px}
.export.right{left:1084px}
.table{position:absolute;top:582px;background:#fff;box-shadow:0 2px 6px rgba(0,0,0,.12);overflow:hidden;border-radius:3px}
.table.stats{left:97px;width:369px}
.table.trades{left:503px;width:665px}
.thead{height:65px;background:var(--black);color:#fff;display:flex;font-family:"Montserrat",sans-serif;font-weight:500;font-size:16px}
.thead div{display:flex;align-items:center;justify-content:center;border-right:1px solid #333}
.thead div:last-child{border-right:none}
.tbody{position:relative}
.row{height:64px;display:flex;font-family:"Roboto Condensed",sans-serif;font-size:16px}
.row:nth-child(even){background:var(--row-alt)}
.row div{display:flex;align-items:center;justify-content:center;border-right:1px solid #e8e8e8}
.stats .c1,.stats .c2{width:166px}
.stats .thead div{width:332px}
.trades .col{width:166px}
.trades .col.last{width:130px}
.scroll{position:absolute;right:0;top:0;width:37px;height:384px;background:#d6d6d6}
.scroll .track{position:absolute;left:10px;top:22px;width:17px;height:345px;background:#fff;border-radius:9px}
.scroll .thumb{position:absolute;left:10px;top:22px;width:17px;height:76px;background:#8f8f8f;border-radius:9px}
</style>
</head>
<body>
<div class="page"></div>

<nav class="topnav">
  <div class="item brand">QVANTA</div>
  <div class="item term">250D</div>
  <div class="item term">83D</div>
  <div class="item term">42D</div>
  <div class="item spacer"></div>
  <div class="item models">
    <svg width="22" height="20" viewBox="0 0 22 20"><path d="M11 1 1 10h3v9h5v-6h4v6h5v-9h3z" fill="none" stroke="#111" stroke-width="2.2" stroke-linejoin="round"/></svg>MODELS</div>
  <div class="item sens">
    <svg width="22" height="22" viewBox="0 0 22 22" fill="#111"><circle cx="11" cy="11" r="2.5"/><circle cx="11" cy="3" r="1.6"/><circle cx="11" cy="19" r="1.6"/><circle cx="3" cy="11" r="1.6"/><circle cx="19" cy="11" r="1.6"/><circle cx="5.3" cy="5.3" r="1.6"/><circle cx="16.7" cy="16.7" r="1.6"/><circle cx="16.7" cy="5.3" r="1.6"/><circle cx="5.3" cy="16.7" r="1.6"/><circle cx="11" cy="7" r="1.1"/><circle cx="11" cy="15" r="1.1"/><circle cx="7" cy="11" r="1.1"/><circle cx="15" cy="11" r="1.1"/></svg>SENSITIVITIES</div>
  <div class="item port">
    <svg width="22" height="22" viewBox="0 0 22 22" fill="none" stroke="#111" stroke-width="2"><circle cx="6" cy="6" r="4"/><circle cx="16" cy="6" r="4"/><circle cx="6" cy="16" r="4"/><circle cx="16" cy="16" r="4"/></svg>PORTFOLIO</div>
  <div class="item backtest">
    <svg width="24" height="20" viewBox="0 0 24 20" fill="none" stroke="#fff" stroke-width="2"><rect x="1" y="1" width="22" height="18" rx="1"/><path d="M5 15l5-6 4 3 5-7"/></svg>BACKTEST</div>
</nav>

<section class="chart-card">
  <div class="tabbar"></div>
  <div class="tab chart">CHART</div>
  <div class="tab t1">#1</div>
  <div class="tab t2">#2</div>
  <div class="tab t3">#3</div>
  <div class="tab t4">#4</div>
  <svg class="plot" width="1071" height="393" viewBox="105 115 1160 425" aria-label="Backtest scatter chart">
    <g stroke="var(--grid)" stroke-width="1">
      <line x1="190" y1="263" x2="1112" y2="263"/><line x1="190" y1="300" x2="1112" y2="300"/>
      <line x1="190" y1="337" x2="1112" y2="337"/><line x1="190" y1="375" x2="1112" y2="375"/>
      <line x1="190" y1="412" x2="1112" y2="412"/>
      <line x1="360" y1="250" x2="360" y2="450"/><line x1="500" y1="250" x2="500" y2="450"/>
      <line x1="640" y1="250" x2="640" y2="450"/><line x1="777" y1="250" x2="777" y2="450"/>
      <line x1="917" y1="250" x2="917" y2="450"/><line x1="1057" y1="250" x2="1057" y2="450"/>
    </g>
    <line x1="190" y1="450" x2="1112" y2="450" stroke="var(--axis)" stroke-width="1.5"/>
    <g font-family="Open Sans, sans-serif" font-size="12" fill="#555">
      <g text-anchor="end"><text x="186" y="267">100</text><text x="186" y="304">80</text><text x="186" y="341">60</text><text x="186" y="379">40</text><text x="186" y="416">20</text><text x="186" y="454">0</text></g>
      <g text-anchor="middle"><text x="217" y="476">Jul 2018</text><text x="360" y="476">Sep 2018</text><text x="500" y="476">Nov 2018</text><text x="640" y="476">Jan 2019</text><text x="777" y="476">Mar 2019</text><text x="917" y="476">May 2019</text><text x="1057" y="476">Jul 2019</text></g>
    </g>
    <path d="M305 316h14l-7 7z" fill="#666"/>
    <g stroke-linecap="round" stroke-width="7">
      <line x1="237" y1="263.5" x2="312" y2="263.5" stroke="var(--olive)" stroke-dasharray="0 4.6"/>
      <line x1="800" y1="265.5" x2="1060" y2="265.5" stroke="var(--olive)" stroke-dasharray="0 4.6"/>
      <line x1="625" y1="263" x2="1062" y2="263" stroke="var(--blue)" stroke-dasharray="0 4.6"/>
    </g>
    <g fill="var(--olive)">
      <circle cx="320" cy="272" r="3.6"/><circle cx="322" cy="268" r="3.6"/><circle cx="330" cy="277" r="3.6"/><circle cx="336" cy="266" r="3.6"/><circle cx="340" cy="270" r="3.6"/><circle cx="345" cy="266" r="3.6"/><circle cx="350" cy="270" r="3.6"/><circle cx="355" cy="268" r="3.6"/><circle cx="365" cy="270" r="3.6"/><circle cx="370" cy="274" r="3.6"/>
      <circle cx="372" cy="328" r="3.6"/><circle cx="375" cy="358" r="3.6"/><circle cx="380" cy="380" r="3.6"/><circle cx="385" cy="345" r="3.6"/><circle cx="388" cy="342" r="3.6"/><circle cx="392" cy="362" r="3.6"/><circle cx="398" cy="378" r="3.6"/><circle cx="402" cy="360" r="3.6"/><circle cx="405" cy="355" r="3.6"/><circle cx="410" cy="370" r="3.6"/><circle cx="415" cy="325" r="3.6"/><circle cx="418" cy="330" r="3.6"/><circle cx="422" cy="300" r="3.6"/><circle cx="428" cy="292" r="3.6"/><circle cx="432" cy="290" r="3.6"/><circle cx="436" cy="265" r="3.6"/><circle cx="440" cy="270" r="3.6"/><circle cx="445" cy="268" r="3.6"/><circle cx="448" cy="338" r="3.6"/><circle cx="452" cy="325" r="3.6"/><circle cx="455" cy="350" r="3.6"/><circle cx="460" cy="355" r="3.6"/><circle cx="465" cy="348" r="3.6"/>
      <circle cx="470" cy="400" r="3.6"/><circle cx="474" cy="420" r="3.6"/><circle cx="478" cy="415" r="3.6"/><circle cx="482" cy="410" r="3.6"/><circle cx="486" cy="398" r="3.6"/><circle cx="490" cy="412" r="3.6"/><circle cx="495" cy="405" r="3.6"/><circle cx="498" cy="440" r="3.6"/><circle cx="502" cy="445" r="3.6"/><circle cx="507" cy="438" r="3.6"/><circle cx="512" cy="440" r="3.6"/><circle cx="516" cy="432" r="3.6"/><circle cx="520" cy="428" r="3.6"/><circle cx="525" cy="418" r="3.6"/><circle cx="530" cy="405" r="3.6"/><circle cx="535" cy="400" r="3.6"/><circle cx="540" cy="390" r="3.6"/><circle cx="545" cy="385" r="3.6"/><circle cx="550" cy="395" r="3.6"/><circle cx="555" cy="390" r="3.6"/><circle cx="560" cy="382" r="3.6"/><circle cx="563" cy="348" r="3.6"/><circle cx="566" cy="340" r="3.6"/><circle cx="570" cy="336" r="3.6"/><circle cx="574" cy="340" r="3.6"/>
      <circle cx="578" cy="265" r="3.6"/><circle cx="582" cy="268" r="3.6"/><circle cx="588" cy="262" r="3.6"/><circle cx="592" cy="270" r="3.6"/><circle cx="598" cy="268" r="3.6"/><circle cx="606" cy="272" r="3.6"/><circle cx="610" cy="284" r="3.6"/>
      <circle cx="612" cy="436" r="3.6"/><circle cx="616" cy="440" r="3.6"/><circle cx="624" cy="437" r="3.6"/><circle cx="630" cy="433" r="3.6"/><circle cx="636" cy="440" r="3.6"/><circle cx="640" cy="430" r="3.6"/><circle cx="645" cy="424" r="3.6"/><circle cx="648" cy="436" r="3.6"/><circle cx="652" cy="428" r="3.6"/><circle cx="656" cy="420" r="3.6"/><circle cx="660" cy="432" r="3.6"/><circle cx="665" cy="436" r="3.6"/><circle cx="670" cy="430" r="3.6"/><circle cx="675" cy="438" r="3.6"/><circle cx="678" cy="410" r="3.6"/><circle cx="682" cy="402" r="3.6"/><circle cx="686" cy="398" r="3.6"/><circle cx="690" cy="326" r="3.6"/><circle cx="692" cy="364" r="3.6"/><circle cx="696" cy="378" r="3.6"/><circle cx="700" cy="330" r="3.6"/><circle cx="705" cy="326" r="3.6"/><circle cx="708" cy="286" r="3.6"/><circle cx="716" cy="282" r="3.6"/><circle cx="726" cy="340" r="3.6"/><circle cx="728" cy="406" r="3.6"/><circle cx="734" cy="410" r="3.6"/><circle cx="736" cy="418" r="3.6"/><circle cx="740" cy="284" r="3.6"/><circle cx="744" cy="296" r="3.6"/><circle cx="742" cy="320" r="3.6"/><circle cx="748" cy="320" r="3.6"/><circle cx="752" cy="308" r="3.6"/><circle cx="756" cy="362" r="3.6"/><circle cx="758" cy="272" r="3.6"/><circle cx="764" cy="270" r="3.6"/><circle cx="768" cy="290" r="3.6"/><circle cx="772" cy="282" r="3.6"/><circle cx="778" cy="275" r="3.6"/><circle cx="785" cy="272" r="3.6"/><circle cx="790" cy="268" r="3.6"/><circle cx="795" cy="278" r="3.6"/>
    </g>
    <g fill="var(--blue)">
      <circle cx="238" cy="328" r="3.6"/><circle cx="240" cy="275" r="3.6"/><circle cx="243" cy="268" r="3.6"/><circle cx="255" cy="270" r="3.6"/><circle cx="247" cy="265" r="3.6"/><circle cx="258" cy="344" r="3.6"/><circle cx="262" cy="378" r="3.6"/><circle cx="268" cy="372" r="3.6"/><circle cx="271" cy="390" r="3.6"/><circle cx="274" cy="395" r="3.6"/><circle cx="272" cy="406" r="3.6"/><circle cx="283" cy="382" r="3.6"/><circle cx="288" cy="378" r="3.6"/><circle cx="290" cy="340" r="3.6"/><circle cx="295" cy="365" r="3.6"/><circle cx="300" cy="370" r="3.6"/><circle cx="303" cy="342" r="3.6"/><circle cx="306" cy="365" r="3.6"/><circle cx="310" cy="405" r="3.6"/><circle cx="318" cy="398" r="3.6"/><circle cx="322" cy="380" r="3.6"/><circle cx="328" cy="378" r="3.6"/><circle cx="332" cy="376" r="3.6"/><circle cx="338" cy="395" r="3.6"/><circle cx="343" cy="392" r="3.6"/><circle cx="346" cy="403" r="3.6"/><circle cx="352" cy="398" r="3.6"/><circle cx="357" cy="402" r="3.6"/><circle cx="368" cy="410" r="3.6"/><circle cx="372" cy="430" r="3.6"/><circle cx="378" cy="432" r="3.6"/><circle cx="385" cy="425" r="3.6"/><circle cx="390" cy="420" r="3.6"/><circle cx="395" cy="428" r="3.6"/><circle cx="400" cy="425" r="3.6"/><circle cx="405" cy="420" r="3.6"/><circle cx="412" cy="425" r="3.6"/><circle cx="418" cy="408" r="3.6"/><circle cx="422" cy="400" r="3.6"/><circle cx="428" cy="392" r="3.6"/><circle cx="432" cy="395" r="3.6"/><circle cx="438" cy="410" r="3.6"/><circle cx="442" cy="400" r="3.6"/><circle cx="448" cy="405" r="3.6"/><circle cx="452" cy="392" r="3.6"/><circle cx="458" cy="412" r="3.6"/><circle cx="463" cy="398" r="3.6"/><circle cx="468" cy="446" r="3.6"/><circle cx="472" cy="444" r="3.6"/><circle cx="480" cy="442" r="3.6"/><circle cx="483" cy="430" r="3.6"/><circle cx="488" cy="425" r="3.6"/><circle cx="495" cy="422" r="3.6"/><circle cx="498" cy="320" r="3.6"/><circle cx="502" cy="292" r="3.6"/><circle cx="508" cy="285" r="3.6"/><circle cx="512" cy="300" r="3.6"/><circle cx="514" cy="276" r="3.6"/><circle cx="518" cy="302" r="3.6"/><circle cx="525" cy="298" r="3.6"/><circle cx="530" cy="425" r="3.6"/><circle cx="535" cy="420" r="3.6"/><circle cx="540" cy="410" r="3.6"/><circle cx="545" cy="402" r="3.6"/><circle cx="560" cy="415" r="3.6"/><circle cx="565" cy="380" r="3.6"/><circle cx="568" cy="368" r="3.6"/><circle cx="575" cy="370" r="3.6"/><circle cx="578" cy="285" r="3.6"/><circle cx="582" cy="280" r="3.6"/><circle cx="590" cy="268" r="3.6"/><circle cx="596" cy="275" r="3.6"/><circle cx="604" cy="270" r="3.6"/><circle cx="614" cy="265" r="3.6"/>
    </g>
    <g fill="var(--green)"><circle cx="1036" cy="447" r="3.6"/><circle cx="1041" cy="447" r="3.6"/><circle cx="1046" cy="447" r="3.6"/></g>
    <text x="1167" y="265" font-family="Georgia, serif" font-size="12" fill="#444">Names</text>
    <g>
      <circle cx="1150" cy="261" r="3.6" fill="#8fb3d9"/><circle cx="1150" cy="280" r="3.6" fill="#f2b27a"/><circle cx="1150" cy="299" r="3.6" fill="#4a9a2e"/><circle cx="1150" cy="318" r="3.6" fill="#e08a8a"/><circle cx="1150" cy="336" r="3.6" fill="#c5a8dd"/><circle cx="1150" cy="355" r="3.6" fill="#bba39a"/><circle cx="1150" cy="373" r="3.6" fill="#f0b3d6"/><circle cx="1150" cy="392" r="3.6" fill="#bdbdbd"/><circle cx="1150" cy="410" r="3.6" fill="#b7b53b"/><circle cx="1150" cy="429" r="3.6" fill="#8dd8e3"/><circle cx="1150" cy="448" r="3.6" fill="#3a6fb0"/>
    </g>
  </svg>
</section>

<aside class="options">
  <span>OPTIONS</span>
  <svg class="toggle" width="28" height="28" viewBox="0 0 28 28"><circle cx="14" cy="14" r="13" fill="var(--navy)" stroke="#fff" stroke-width="2"/><path d="M8 14h11M15 10l4 4-4 4" fill="none" stroke="#fff" stroke-width="2" stroke-linecap="round" stroke-linejoin="round"/></svg>
</aside>

<div class="export left"><svg width="24" height="22" viewBox="0 0 24 22" fill="none" stroke="var(--navy)" stroke-width="2.2" stroke-linecap="round" stroke-linejoin="round"><path d="M10 4H3v16h16v-7"/><path d="M9 14c1-6 6-9 12-9M17 1l4 4-4 4"/></svg>Export</div>
<div class="export right"><svg width="24" height="22" viewBox="0 0 24 22" fill="none" stroke="var(--navy)" stroke-width="2.2" stroke-linecap="round" stroke-linejoin="round"><path d="M10 4H3v16h16v-7"/><path d="M9 14c1-6 6-9 12-9M17 1l4 4-4 4"/></svg>Export</div>

<section class="table stats">
  <div class="thead"><div>Stats</div></div>
  <div class="tbody">
    <div class="row"><div class="c1">Stat 1</div><div class="c2">0.5</div></div>
    <div class="row"><div class="c1">Stat 2</div><div class="c2">-3</div></div>
    <div class="row"><div class="c1">Stat 3</div><div class="c2">30%</div></div>
    <div class="row"><div class="c1">Stat 4</div><div class="c2">0.5</div></div>
    <div class="row"><div class="c1">Stat 5</div><div class="c2">-3</div></div>
    <div class="row"><div class="c1">Stat 6</div><div class="c2">30%</div></div>
    <div class="scroll"><div class="track"></div><div class="thumb"></div></div>
  </div>
</section>

<section class="table trades">
  <div class="thead"><div class="col">Open</div><div class="col">Close</div><div class="col">Size</div><div class="col" style="width:167px">Return</div></div>
  <div class="tbody">
    <div class="row"><div class="col">2018-04-05</div><div class="col">2018-04-07</div><div class="col">13</div><div class="col last">5%</div></div>
    <div class="row"><div class="col">2018-04-05</div><div class="col">2018-04-07</div><div class="col">12</div><div class="col last">7%</div></div>
    <div class="row"><div class="col">2018-04-05</div><div class="col">2018-04-07</div><div class="col">15</div><div class="col last">6%</div></div>
    <div class="row"><div class="col">2018-04-05</div><div class="col">2018-04-07</div><div class="col">16</div><div class="col last">9%</div></div>
    <div class="row"><div class="col">2018-04-05</div><div class="col">2018-04-07</div><div class="col">12</div><div class="col last">8%</div></div>
    <div class="row"><div class="col">2018-04-05</div><div class="col">2018-04-07</div><div class="col">19</div><div class="col last">6%</div></div>
    <div class="scroll"><div class="track"></div><div class="thumb"></div></div>
  </div>
</section>
</body>
</html>
```